U.S. Popcorn company needs business cards

We are a popcorn company that manufactures popcorn and sells it to grocery stores worldwide. Our theme is "Americana" and our logo is U.S. route 66 which is the most famous highway in the U.S.

We would like the design to be simple and to use both sides. On the back side we would like to see just the logo and website. The front would be normal details

Target Market(s)

Wholesalers, grocers and distributors

Industry/Entity Type

Manufacture

Contact Information for Business Card

Business name: Prairie Lantern Popcorn
Phone: +1 555 308 4726
Email: Dale@prairielanternpopcorn.com
website: www.prairielanternpopcorn.com
Tag Line: "Crunchy since day one"
Name: Dale Whitcombe
Title: Founder/President

Requirements
Must have
• Either this design should be fun or clean and simple. I will let you show me your thougths.
Nice to have
• Anything that ties in the real Hwy Route 66.
• Colors might need to be red, white and blue incorporated.
Should not have
• Not be too busy.

```html
<!DOCTYPE html>
<html lang="en">
<head>
<meta charset="utf-8">
<title>Prairie Lantern Popcorn – Business Cards</title>
<link href="https://fonts.googleapis.com/css2?family=Lato:wght@400;700&display=swap" rel="stylesheet">
<style>
  :root {
    --stage: #222222;
    --navy: #232f63;
    --red: #e3242b;
    --white: #ffffff;
  }
  * { margin: 0; padding: 0; box-sizing: border-box; }
  html, body { width: 1189px; height: 1200px; overflow: hidden; background: var(--stage); }
  body { position: relative; font-family: 'Lato', sans-serif; }

  .card { position: absolute; left: 171px; width: 855px; height: 488px; box-shadow: 0 2px 6px rgba(0,0,0,0.5); overflow: hidden; }

  /* back side */
  .card-back { top: 67px; background: var(--navy); color: var(--white); text-align: center; }
  .card-back .brand-name { position: absolute; left: 0; right: 0; top: 198px; font-size: 48px; line-height: 58px; font-weight: 700; letter-spacing: 0.5px; }
  .card-back .brand-url { position: absolute; left: 0; right: 0; top: 266px; font-size: 24px; line-height: 30px; font-weight: 400; }

  /* front side */
  .card-front { top: 626px; background: var(--white); }
  .brand-panel { position: absolute; left: 0; top: 0; width: 434px; height: 100%; background: var(--white); }
  .brand-mark { position: absolute; left: 0; right: 0; top: 170px; text-align: center; color: var(--navy); font-weight: 700; font-size: 36px; line-height: 1.15; }
  .brand-mark .dot { display: block; width: 44px; height: 44px; margin: 0 auto 16px; border-radius: 50%; background: var(--red); }
  .tagline { position: absolute; left: 0; right: 0; top: 360px; text-align: center; color: var(--red); font-size: 23px; }

  .divider { position: absolute; left: 434px; top: 0; width: 4px; height: 100%; background: var(--red); }
  .details-panel { position: absolute; left: 442px; top: 0; right: 0; height: 100%; background: var(--navy); color: var(--white); }
  .company { position: absolute; left: 26px; top: 62px; font-size: 32px; line-height: 40px; font-weight: 700; }
  .person-name { position: absolute; left: 26px; top: 159px; font-size: 28px; line-height: 34px; }
  .person-title { position: absolute; left: 26px; top: 190px; font-size: 21px; line-height: 24px; color: var(--red); }
  .address { position: absolute; left: 28px; top: 252px; font-size: 21px; line-height: 28px; }
  .contact-list { position: absolute; left: 28px; top: 340px; list-style: none; font-size: 19.5px; }
  .contact-list li { display: flex; align-items: center; height: 28px; }
  .contact-list svg { width: 20px; height: 20px; margin-right: 14px; flex: none; }
</style>
</head>
<body>

<section class="card card-back" aria-label="Business card back">
  <h1 class="brand-name">PRAIRIE LANTERN POPCORN</h1>
  <p class="brand-url">www.prairielanternpopcorn.com</p>
</section>

<section class="card card-front" aria-label="Business card front">
  <div class="brand-panel">
    <div class="brand-mark"><span class="dot"></span>Prairie Lantern<br>Popcorn</div>
    <p class="tagline">Crunchy since day one</p>
  </div>
  <div class="divider"></div>
  <div class="details-panel">
    <h2 class="company">Prairie Lantern Popcorn</h2>
    <p class="person-name">Dale Whitcombe</p>
    <p class="person-title">Founder/President</p>
    <p class="address">Millbrook, KS<br>United States</p>
    <ul class="contact-list">
      <li>
        <svg viewBox="0 0 20 20" aria-hidden="true"><path fill="#e3242b" d="M2 7c0-3 4-4 8-4s8 1 8 4v1h-4V6.5c-1-.6-2.5-.8-4-.8s-3 .2-4 .8V8H2z M5 9h10l2 8H3z"/><circle cx="10" cy="13" r="2" fill="#232f63"/></svg>
        +1 555 308 4726
      </li>
      <li>
        <svg viewBox="0 0 20 20" aria-hidden="true"><rect x="1" y="4" width="18" height="12" fill="#e3242b"/><path d="M1 4l9 7 9-7M1 16l7-6M19 16l-7-6" stroke="#232f63" stroke-width="1.3" fill="none"/></svg>
        Dale@prairielanternpopcorn.com
      </li>
      <li>
        <svg viewBox="0 0 20 20" aria-hidden="true"><circle cx="10" cy="10" r="8.5" fill="#e3242b"/><path d="M4 6c2 0 3 1 3 3s2 2 2 4-1 3-1 4M12 3c0 2 2 2 3 3s0 3 2 4" stroke="#232f63" stroke-width="1.5" fill="none"/></svg>
        www.prairielanternpopcorn.com
      </li>
    </ul>
  </div>
</section>

</body>
</html>
```